Varnik Holdings — Business Card Design Brief
Overview
Design a double-sided business card for Varnik Holdings that highlights our two service arms: Varnik Communications (telecommunications) and Varnik Energy (business energy solutions). The card should feel smart and stand out when handed to clients.

Objectives
Showcase our areas of specialty clearly.
Reflect the overall Varnik / Varnik Holdings brand while acknowledging both arms.
Explore using both logos (Communications + Energy) or one unified logo, depending on the design.

Deliverables
One double-sided business card design (front + back).

Content & Copy
Front (preferred): Logo: Varnik / Varnik Holdings
Descriptor: Business Communications | Business Energy
Back:My contact details and company details
Core products: Business Mobile • Telephony • Internet • Business Energy Solutions

Brand & Visual Direction
We have a group logo currently tailored more toward telecoms, plus a separate Varnik Energy logo.
Please explore layouts that use both logos or just one, whichever works best.
Color: I wouldn't mind seeing an option using our the Blue/Purple gradient from our website (varnik-example.co.uk), but also open to non-gradient approaches and other colours..

Overall look: Smart, modern, and distinctive.
Format & Print Specs
Double-sided business card format. (Use a standard size

Must-Haves
Front: Varnik wording or Varnik Holdings wording with atleast 1 logo also on front “Business Communications | Business Energy.”

Back: Contact + company details and core products.
A design that stands out while remaining professional.

Nice-to-Have Options
A gradient version using our site’s Blue/Purple gradient.
A non-gradient version.
A dual-logo treatment versus a single-logo treatment.

Thanks
Owen

```html
<!DOCTYPE html>
<html lang="en">
<head>
<meta charset="utf-8">
<title>Varnik Holdings — Business Card</title>
<link href="https://fonts.googleapis.com/css2?family=Montserrat:wght@700&family=Roboto:wght@400&display=swap" rel="stylesheet">
<style>
  :root {
    --backdrop: #e4e4e4;
    --card-white: #ffffff;
    --navy: #1b1464;
    --green: #3fa535;
    --lime: #c8d400;
    --ink: #333333;
    --rule: #cfcfcf;
    --faint-blue: #e8f3fb;
    --grad-top: #0bb4e4;
    --grad-bottom: #0a58d0;
    --white: #ffffff;
  }
  * { box-sizing: border-box; margin: 0; padding: 0; }
  html, body { width: 1200px; height: 1200px; overflow: hidden; }
  body { background: var(--backdrop); position: relative; font-family: "Roboto", Arial, sans-serif; }

  .card { position: absolute; left: 262px; width: 688px; height: 393px; overflow: hidden; }
  .card-front { top: 159px; background: var(--card-white); }
  .card-back { top: 653px; background: linear-gradient(180deg, var(--grad-top), var(--grad-bottom)); }

  .faint-ring { position: absolute; left: 6px; top: 168px; width: 200px; height: 200px; border-radius: 50%; border: 14px solid var(--faint-blue); }

  .brand { position: absolute; right: 47px; top: 142px; display: flex; align-items: center; gap: 12px; }
  .brand-dot { width: 26px; height: 26px; border-radius: 50%; background: var(--green); }
  .brand-name { font-family: "Montserrat", Arial, sans-serif; font-weight: 700; font-size: 48px; color: var(--navy); letter-spacing: 1px; line-height: 1; }

  .person { position: absolute; left: 48px; top: 196px; }
  .person-name { font-family: "Montserrat", Arial, sans-serif; font-weight: 700; font-size: 26px; color: var(--navy); line-height: 1.1; letter-spacing: 0.3px; }
  .person-title { font-size: 16px; color: var(--green); margin-top: 2px; }

  .divider { position: absolute; left: 213px; right: 47px; top: 255px; height: 1px; background: var(--rule); }

  .contacts { position: absolute; left: 48px; top: 265px; list-style: none; font-size: 17px; color: var(--ink); }
  .contacts li { display: flex; align-items: center; height: 20px; }
  .contacts svg { width: 14px; height: 14px; margin-right: 8px; fill: var(--navy); }

  .address { position: absolute; right: 44px; top: 266px; text-align: right; font-size: 17px; line-height: 20.5px; color: var(--ink); }

  .products { position: absolute; left: 0; right: 0; top: 340px; text-align: center; font-size: 17px; color: #222; }
  .products .sep { margin: 0 6px; }

  .stripe { position: absolute; left: 0; right: 0; top: 372px; height: 3px; background: linear-gradient(90deg, var(--green), var(--lime)); }
  .band { position: absolute; left: 0; right: 0; top: 377px; bottom: 0; background: var(--navy); }

  .arm { position: absolute; top: 150px; width: 270px; text-align: center; color: var(--white); }
  .arm-comms { left: 71px; }
  .arm-energy { left: 348px; }
  .arm-mark { display: flex; align-items: center; justify-content: center; gap: 12px; height: 72px; }
  .arm-dot { width: 22px; height: 22px; border-radius: 50%; background: var(--white); }
  .arm-name { font-family: "Montserrat", Arial, sans-serif; font-weight: 700; font-size: 38px; letter-spacing: 1px; }
  .arm-label { font-size: 17px; margin-top: 40px; letter-spacing: 0.2px; }
  .arm-divider { position: absolute; left: 345px; top: 114px; width: 1px; height: 167px; background: rgba(255,255,255,0.8); }
</style>
</head>
<body>

<section class="card card-front" aria-label="Card front">
  <div class="faint-ring"></div>

  <div class="brand">
    <span class="brand-dot"></span>
    <span class="brand-name">VARNIK</span>
  </div>

  <div class="person">
    <p class="person-name">DANIEL MERCER</p>
    <p class="person-title">President</p>
  </div>

  <div class="divider"></div>

  <ul class="contacts">
    <li><svg viewBox="0 0 24 24"><path d="M6.6 10.8a15 15 0 0 0 6.6 6.6l2.2-2.2c.3-.3.7-.4 1-.2 1.1.4 2.3.6 3.6.6.6 0 1 .4 1 1V20c0 .6-.4 1-1 1C10.6 21 3 13.4 3 4c0-.6.4-1 1-1h3.5c.6 0 1 .4 1 1 0 1.3.2 2.5.6 3.6.1.3 0 .7-.2 1z"/></svg>736-555-0142</li>
    <li><svg viewBox="0 0 24 24"><path d="M7 1h10a2 2 0 0 1 2 2v18a2 2 0 0 1-2 2H7a2 2 0 0 1-2-2V3a2 2 0 0 1 2-2zm0 3v14h10V4z"/></svg>736-555-0187</li>
    <li><svg viewBox="0 0 24 24"><path d="M2 5h20v14H2zm2 2v.5l8 5 8-5V7zm0 2.8V17h16V9.8l-8 5z"/></svg>info@varnik-example.co.uk</li>
  </ul>

  <address class="address" style="font-style:normal">
    214 Fenwick Row<br>
    Halverton, Canada 512<br>
    www.varnik-example.co.uk
  </address>

  <p class="products">Business Mobile<span class="sep">•</span>Telephony<span class="sep">•</span>Internet<span class="sep">•</span>Business Energy Solutions</p>

  <div class="stripe"></div>
  <div class="band"></div>
</section>

<section class="card card-back" aria-label="Card back">
  <div class="arm arm-comms">
    <div class="arm-mark"><span class="arm-dot"></span><span class="arm-name">VARNIK</span></div>
    <p class="arm-label">BUSINESS COMMUNICATIONS</p>
  </div>
  <div class="arm-divider"></div>
  <div class="arm arm-energy">
    <div class="arm-mark"><span class="arm-dot"></span><span class="arm-name">VARNIK</span></div>
    <p class="arm-label">BUSINESS ENERGY</p>
  </div>
</section>

</body>
</html>
```